Wholesale food company needs a package for Carp boilies (fishing)

We need a (5kg) doypack with handle design for a new brand here in the BENELUX called Tolvo Lures. We already have a logo but we need a flashing design to promote it on shows and webshops. The design must also include some transparant places so you can see the product inside. We have added the logo and the website is www.tolvolures.nl. You can look for an impression at http://marwick-goods.nl/product-category/baits/specials/

Target Market(s)

Carpf fishing and coarse angling

Industry/Entity Type

It Company

Requirements
Must have
• A slogan that suits both types of fishing.
• Extra information doypack:
• Material: PET/PE
• Thickness: 12µ/120µ
• Size: B 320 x H 450 MM

```html
<!DOCTYPE html>
<html lang="en">
<head>
<meta charset="utf-8">
<title>Tolvo Lures – Doypack Front and Back</title>
<link rel="stylesheet" href="https://fonts.googleapis.com/css2?family=Open+Sans:wght@400;700&display=swap">
<style>
  :root {
    --page-bg: #ffffff;
    --handle-light: #4cc8ef;
    --handle-dark: #3b4fa0;
    --panel-light: #6bb2e2;
    --panel-mid: #0a8fd0;
    --panel-dark: #0b72bb;
    --band-green: #6cbb5a;
    --bait-green: #5ee04a;
    --bait-deep: #2fae2b;
    --white: #ffffff;
    --ink: #3a3a3a;
    --measure-grey: #c8c8c8;
    --measure-dark: #555555;
    --measure-red: #e53935;
    --outline: #9a9a9a;
  }
  html, body {
    margin: 0;
    padding: 0;
    width: 1200px;
    height: 892px;
    overflow: hidden;
    background: var(--page-bg);
  }
  .sheet { display: block; width: 1200px; height: 892px; }
  .brand-name { font-family: "Open Sans", Arial, sans-serif; font-weight: 700; font-size: 40px; fill: var(--white); }
  .brand-line { font-family: "Open Sans", Arial, sans-serif; font-weight: 700; font-size: 22px; letter-spacing: 2px; fill: var(--white); }
  .claim { font-family: "Open Sans", Arial, sans-serif; font-weight: 700; font-size: 19px; fill: var(--white); }
  .web-front { font-family: "Open Sans", Arial, sans-serif; font-weight: 700; font-size: 21px; fill: var(--white); }
  .web-back { font-family: "Open Sans", Arial, sans-serif; font-weight: 700; font-size: 21px; fill: var(--ink); }
  .ingredients-note { font-family: "Open Sans", Arial, sans-serif; font-size: 18px; fill: var(--ink); }
  .measure { font-family: "Open Sans", Arial, sans-serif; font-size: 22px; }
  .measure-grey { fill: var(--measure-grey); }
  .measure-dark { fill: var(--measure-dark); }
  .measure-red { fill: var(--measure-red); }
</style>
</head>
<body>
<svg class="sheet" viewBox="0 0 1200 892" xmlns="http://www.w3.org/2000/svg">
  <defs>
    <linearGradient id="handle-grad" x1="0" y1="0" x2="1" y2="0.4">
      <stop offset="0" stop-color="var(--handle-light)"/>
      <stop offset="1" stop-color="var(--handle-dark)"/>
    </linearGradient>
    <linearGradient id="panel-grad" x1="0" y1="0" x2="1" y2="0">
      <stop offset="0" stop-color="var(--panel-light)"/>
      <stop offset="0.15" stop-color="var(--panel-mid)"/>
      <stop offset="0.85" stop-color="var(--panel-dark)"/>
      <stop offset="1" stop-color="var(--panel-light)"/>
    </linearGradient>
    <radialGradient id="bait-grad" cx="0.5" cy="0.5" r="0.7">
      <stop offset="0" stop-color="var(--bait-green)"/>
      <stop offset="1" stop-color="var(--bait-deep)"/>
    </radialGradient>
  </defs>

  <!-- Front panel -->
  <g class="panel panel-front">
    <path class="handle" d="M69 140 V100 Q69 37 132 37 H472 Q534 37 534 100 V140 Z" fill="url(#handle-grad)"/>
    <path class="handle-hole" d="M227 78 H283 Q285 56 302 56 Q320 56 322 78 H377 Q397 78 397 98 Q397 118 377 118 H227 Q207 118 207 98 Q207 78 227 78 Z" fill="var(--white)"/>
    <rect class="body" x="69" y="140" width="465" height="652" fill="url(#panel-grad)" stroke="var(--outline)" stroke-width="1"/>

    <text class="brand-name" x="301" y="208" text-anchor="middle">TOLVO LURES</text>
    <text class="brand-line" x="301" y="242" text-anchor="middle">CARP PRODUCTS</text>

    <path class="claim-band" d="M69 268 Q300 230 534 268 V383 Q300 345 69 383 Z" fill="var(--band-green)"/>
    <text class="claim" x="301" y="313" text-anchor="middle">Eco Friendly | Premium Quality</text>
    <text class="claim" x="301" y="343" text-anchor="middle">100% Fresh | High Attraction</text>

    <path class="product-window" role="img" aria-label="Transparent window showing bright green carp boilies"
          d="M69 460 Q150 430 230 455 Q320 420 420 450 Q480 435 534 455 V625 Q470 600 410 620 Q320 600 250 630 Q160 610 69 630 Z"
          fill="url(#bait-grad)"/>

    <text class="web-front" x="302" y="759" text-anchor="middle">www.tolvolures.nl</text>
  </g>

  <!-- Back panel -->
  <g class="panel panel-back">
    <path class="handle" d="M633 140 V100 Q633 37 696 37 H1036 Q1098 37 1098 100 V140 Z" fill="url(#handle-grad)"/>
    <path class="handle-hole" d="M791 78 H847 Q849 56 866 56 Q884 56 886 78 H941 Q961 78 961 98 Q961 118 941 118 H791 Q771 118 771 98 Q771 78 791 78 Z" fill="var(--white)"/>
    <rect class="body" x="633" y="140" width="465" height="652" fill="var(--white)" stroke="var(--outline)" stroke-width="1"/>
    <path class="top-field" d="M633 140 H1098 V470 Q1060 450 1020 470 Q960 500 900 480 Q850 440 800 445 Q740 420 690 460 Q660 475 633 470 Z" fill="url(#panel-grad)"/>

    <text class="brand-name" x="866" y="208" text-anchor="middle">TOLVO LURES</text>
    <text class="brand-line" x="866" y="242" text-anchor="middle">CARP PRODUCTS</text>

    <text class="ingredients-note" x="866" y="618" text-anchor="middle">here ingredients lable come.</text>
    <text class="web-back" x="866" y="759" text-anchor="middle">www.tolvolures.nl</text>
  </g>

  <!-- Dimension notes -->
  <g class="measures">
    <text class="measure measure-grey" transform="translate(56 125) rotate(-90)">70mm</text>
    <text class="measure measure-grey" transform="translate(56 465) rotate(-90)">450mm</text>
    <text class="measure measure-red" x="258" y="827">320mm</text>
    <text class="measure measure-red" x="406" y="827">font</text>
    <text class="measure measure-dark" x="838" y="827">320mm</text>
    <text class="measure measure-dark" x="1036" y="827">back</text>
  </g>
</svg>
</body>
</html>
```